PHGCCUL re-branding website and logo

We are looking for a new webpage design and logo our current page address is www.phgccul-example.org. We want to create a new design using PHGCCUL Pinewood and Harbour Growers Co-operative Credit Union limited and another with the purposed new name PHFC Pinewood and Harbour Financial Co-operative, the color scheme is purple and burnt orange. Our new logo and webpage should communicate change and growth purposed theme continuing our legacy here to server past, present and future generations. Our idea for the logo is a live shot of hands of different ages in a circle holding a tree

Target Market(s)

Everyone

Contact Information for Business Card

Company Name
Telephone number
Address
slot to enter employee info

Logo Text

(P & H) Pinewood And Harbour Financial Co-operative

Coding

Coded - Design and coding required

Number of Pages Required

2 page

Colors
f37122
fbed22
6b449b

Requirements
Must have
• links for social media

```html
<!DOCTYPE html>
<html lang="en">
<head>
<meta charset="utf-8">
<title>PHFC – Pinewood and Harbour Financial Co-operative</title>
<link href="https://fonts.googleapis.com/css2?family=Open+Sans:ital,wght@0,400;0,600;0,700;1,600;1,700&display=swap" rel="stylesheet">
<style>
:root{
  --orange:#f37122;
  --orange-dark:#e0601a;
  --purple:#6b449b;
  --purple-light:#8555c0;
  --yellow:#fbed22;
  --black:#050505;
  --ink:#2e2e2e;
  --body:#555;
  --grey-bg:#f3f3f3;
  --footer-dark:#2b2b2b;
  --rule:#dcdcdc;
}
*{box-sizing:border-box;margin:0;padding:0}
html,body{width:1200px;height:2462px;overflow:hidden}
body{font-family:'Open Sans',sans-serif;color:var(--ink);background:#fff;position:relative}
.abs{position:absolute}
a{color:inherit;text-decoration:none}

/* header */
.topbar{left:0;top:0;width:1200px;height:141px;background:var(--black)}
.topbar::before{content:"";position:absolute;left:0;top:0;width:100%;height:6px;
  background:linear-gradient(90deg,var(--orange) 0 33%,var(--purple) 33% 66%,var(--yellow) 66%)}
.brand{left:77px;top:50px}
.brand-name{color:#fff;font-weight:700;font-size:30px;letter-spacing:1px;line-height:40px}
.contact{top:58px;display:flex;align-items:center;gap:10px;color:#fff;font-weight:700;font-size:19px}
.contact svg{width:20px;height:20px;fill:var(--yellow)}
.teller{left:885px;top:48px;width:241px;height:54px;border:2px solid #fff;border-radius:3px;
  display:flex;align-items:center;justify-content:center;gap:10px;color:var(--yellow);font-weight:700;font-size:13px}
.teller svg{width:18px;height:18px;fill:var(--yellow)}

.mainnav{left:0;top:141px;width:1200px;height:54px;background:linear-gradient(var(--orange),var(--orange-dark))}
.mainnav a{position:absolute;top:17px;color:#fff;font-size:14px;font-weight:600;white-space:nowrap}
.mainnav a.active{font-weight:700}

/* hero */
.hero{left:0;top:195px;width:1200px;height:481px;
  background:linear-gradient(90deg,#f6f5f2 0%,#eceae4 35%,#b9c7a8 60%,#8aa2c4 80%,#e8e6e2 100%)}
.hero-title{left:75px;top:350px;font-size:38px;font-weight:700;line-height:46px;color:var(--ink);letter-spacing:.5px}
.btn{display:flex;align-items:center;justify-content:center;width:165px;height:43px;
  background:linear-gradient(var(--orange),var(--orange-dark));color:#fff;font-weight:700;font-size:13px}
.dots{left:75px;top:540px;display:flex;gap:5px}
.dots i{width:9px;height:9px;border-radius:50%;background:#777}
.dots i:first-child{background:var(--purple)}

/* feature band */
.features{left:75px;top:702px;width:1051px;height:198px;display:flex;
  background:linear-gradient(var(--purple-light),var(--purple))}
.feature{flex:1;display:flex;flex-direction:column;align-items:center;padding-top:42px;border-right:1px solid rgba(255,255,255,.12)}
.feature:last-child{border-right:0}
.feature-icon{width:80px;height:80px;border:2px solid #fff;border-radius:50%;display:flex;align-items:center;justify-content:center}
.feature-icon svg{width:38px;height:38px;fill:none;stroke:var(--yellow);stroke-width:2.4}
.feature-label{margin-top:26px;color:var(--yellow);font-weight:700;font-size:15px}

/* about */
.about{left:75px;top:942px;width:600px}
.section-title{font-size:28px;font-weight:700;color:var(--ink);letter-spacing:.5px}
.about-sub{color:var(--orange);font-style:italic;font-weight:600;font-size:21px;margin-top:2px}
.about p{margin-top:14px;font-size:13.6px;line-height:24.6px;color:var(--body);width:600px}
.about .btn{margin-top:28px}
.about-photo{left:706px;top:950px;width:420px;height:270px;
  background:linear-gradient(135deg,#b7cde4,#4f6f93 55%,#1c2838)}

/* notice */
.notice{left:0;top:1276px;width:1200px;height:352px;background:var(--grey-bg)}
.notice-photo{left:0;top:0}
.notice-text{left:75px;top:1330px}
.notice-title{font-size:36px;font-weight:700;line-height:42px;color:var(--purple);letter-spacing:.5px}
.notice-lead{margin-top:16px;font-size:13.5px;font-weight:700;color:var(--ink)}
.notice-date{margin-top:6px;font-size:19px;font-weight:700;color:var(--purple)}
.notice-text .btn{margin-top:28px}

/* panels */
.panel{top:1676px;width:510px;height:357px;border:1px solid var(--rule);background:#fff}
.panel-head{height:48px;background:var(--purple);color:var(--yellow);font-size:27px;font-weight:700;padding:4px 20px}
.panel-body{padding:12px 20px 0}
.rate{border-bottom:1px solid var(--rule);padding:7px 0 9px}
.rate-name{color:var(--orange);font-weight:700;font-size:15px}
.rate-row{display:flex;justify-content:space-between;font-size:13px;color:var(--ink);margin-top:4px}
.rate-row b{color:var(--purple);font-size:15px}
.rate-row b small{font-size:11px}
.rate-note{font-size:11.5px;padding-top:12px;color:var(--ink)}
.rate-note a{color:var(--purple);font-weight:600;margin-left:6px}
.news-item{border-bottom:1px solid var(--rule);padding:10px 0 14px}
.news-item h3{color:var(--orange);font-size:15px;font-weight:700}
.news-item p{font-size:13px;line-height:22.5px;color:var(--body);margin-top:6px}
.news-item time{display:block;color:var(--purple);font-weight:700;font-size:13px;margin-top:6px}
.news-all{text-align:right;font-size:11.5px;font-weight:700;color:var(--purple);padding-top:12px}

/* footer */
.footer{left:0;top:2080px;width:1200px;height:292px;background:var(--grey-bg)}
.fcol{top:2122px;font-size:12.5px;color:var(--body)}
.fcol h4{font-size:14px;color:var(--purple);font-weight:700;margin-bottom:8px}
.fcol h5{font-size:13px;color:var(--ink);font-weight:700;margin-bottom:6px}
.fcol li{list-style:none;line-height:26.8px}
.fcol .ic{display:inline-flex;width:26px}
.fcol .ic svg{width:12px;height:12px;fill:#444}
.bottom{left:0;top:2372px;width:1200px;height:90px;background:var(--footer-dark);color:#999;font-size:11.5px}
.bottom .copy{position:absolute;left:75px;top:25px;line-height:22px}
.bottom .copy b{color:#fff}
.social{position:absolute;left:960px;top:32px;display:flex;gap:16px}
.social span{width:18px;height:18px;border-radius:50%;background:#cfcfcf}
</style>
</head>
<body>

<header class="abs topbar">
  <div class="abs brand">
    <span class="brand-name">P &amp; H</span>
  </div>
  <div class="abs contact" style="left:493px">
    <svg viewBox="0 0 24 24"><path d="M6.6 10.8a15 15 0 0 0 6.6 6.6l2.2-2.2c.3-.3.7-.4 1-.2 1.1.4 2.3.6 3.6.6.6 0 1 .4 1 1V20c0 .6-.4 1-1 1A17 17 0 0 1 3 4c0-.6.4-1 1-1h3.5c.6 0 1 .4 1 1 0 1.3.2 2.5.6 3.6.1.3 0 .7-.2 1z"/></svg>
    (555) 410-2200
  </div>
  <div class="abs contact" style="left:696px">
    <svg viewBox="0 0 24 24"><path d="M6 2h9l3 3v4h2a2 2 0 0 1 2 2v9a2 2 0 0 1-2 2H4a2 2 0 0 1-2-2v-9a2 2 0 0 1 2-2h2zm2 2v5h8V6h-2V4zm-2 9v2h3v-2zm5 0v2h3v-2zm5 0v2h3v-2zm-10 4v2h3v-2zm5 0v2h3v-2zm5 0v2h3v-2z"/></svg>
    (555) 410-2291
  </div>
  <a class="abs teller" href="#">
    <svg viewBox="0 0 24 24"><path d="M4 5h16v10H4zm2 2v6h12V7zM1 17h22v2H1z"/></svg>
    INTERNET TELLER LOGIN ›
  </a>
</header>

<nav class="abs mainnav">
  <a class="active" href="#" style="left:75px">HOME</a>
  <a href="#" style="left:159px">APPLY FOR A LOAN</a>
  <a href="#" style="left:332px">MY CREDIT UNION</a>
  <a href="#" style="left:499px">PRODUCTS &amp; SERVICES</a>
  <a href="#" style="left:696px">BECOME A MEMBER</a>
  <a href="#" style="left:873px">TOOLS &amp; BENEFITS</a>
  <a href="#" style="left:1042px">LOCATIONS</a>
</nav>

<section class="abs hero" role="img" aria-label="Photograph of a smiling woman working through paperwork with a calculator and laptop at a desk"></section>
<h1 class="abs hero-title">PINEWOOD &amp; HARBOUR<br>FINANCIAL CO-OPERATIVE</h1>
<a class="abs btn" href="#" style="left:75px;top:471px">READ MORE</a>
<div class="abs dots"><i></i><i></i><i></i><i></i></div>

<section class="abs features">
  <div class="feature">
    <div class="feature-icon"><svg viewBox="0 0 40 40"><rect x="6" y="11" width="28" height="18"/><circle cx="20" cy="20" r="5"/></svg></div>
    <div class="feature-label">MY CREDIT UNION</div>
  </div>
  <div class="feature">
    <div class="feature-icon"><svg viewBox="0 0 40 40"><rect x="6" y="10" width="28" height="20" rx="2"/><path d="M6 16h28M11 24h8"/></svg></div>
    <div class="feature-label">PRODUCTS &amp; SERVICES</div>
  </div>
  <div class="feature">
    <div class="feature-icon"><svg viewBox="0 0 40 40"><rect x="9" y="10" width="22" height="15"/><path d="M4 29h32"/></svg></div>
    <div class="feature-label">TOOLS &amp; BENEFITS</div>
  </div>
</section>

<section class="abs about">
  <h2 class="section-title">ABOUT PHFC</h2>
  <div class="about-sub">Pinewood and Harbour Financial Co-operative</div>
  <p>Aliquam molestie, mi et imperdiet euismod, dui purus auctor tellus, et interdum lacus lectus et ante. Sed accumsan sollicitudin sapien, sit amet adipiscing turpis gravida ac. In congue, neque ac lobortis volutpat, libero mauris varius mi, vitae suscipit ipsum ligula vitae risus. Duis aliquam nibh a dui iaculis viverra id a velit. Vivamus egestas risus in magna varius commodo. Sed semper viverra egestas.</p>
  <a class="btn" href="#">READ MORE</a>
</section>
<div class="abs about-photo" role="img" aria-label="Close-up photograph of a bank card resting on a calculator keypad"></div>

<section class="abs notice">
  <svg class="abs notice-photo" width="1200" height="352" role="img" aria-label="Photograph of a young woman holding a bank card at an ATM">
    <defs><linearGradient id="atm" x1="0" y1="0" x2="1" y2="0">
      <stop offset="0" stop-color="#4a4d52"/><stop offset=".45" stop-color="#9aa6ad"/><stop offset="1" stop-color="#5d6b64"/>
    </linearGradient></defs>
    <polygon points="673,0 1200,0 1200,352 601,352" fill="url(#atm)"/>
  </svg>
</section>
<div class="abs notice-text">
  <h2 class="notice-title">ATM CARDS<br>RENEWAL NOTICE</h2>
  <div class="notice-lead">Please be adviced that all ATM Cards issued February 2014 ,</div>
  <div class="notice-date">Expires Effective February28, 2017</div>
  <a class="btn" href="#">READ MORE</a>
</div>

<section class="abs panel" style="left:75px">
  <div class="panel-head">FEATURED RATES</div>
  <div class="panel-body">
    <div class="rate"><div class="rate-name">Consumer Loans</div><div class="rate-row"><span>as low as</span><b>9.00% <small>APR*</small></b></div></div>
    <div class="rate"><div class="rate-name">New Auto/Motorcycle</div><div class="rate-row"><span>as low as</span><b>7.00% <small>APR*</small></b></div></div>
    <div class="rate"><div class="rate-name">Used Auto/Motorcycle</div><div class="rate-row"><span>as low as</span><b>11.75% <small>APR*</small></b></div></div>
    <div class="rate"><div class="rate-name">Mortgages</div><div class="rate-row"><span>as low as</span><b>8.25% <small>APR*</small></b></div></div>
    <div class="rate-note">*APR - Annual Percentage Rate. <a href="#">Apply For A Loan ›</a></div>
  </div>
</section>

<section class="abs panel" style="left:616px">
  <div class="panel-head">NEWS &amp; EVENTS</div>
  <div class="panel-body">
    <article class="news-item"><h3>Nam fermentum vestibulum purus</h3><p>Duis aliquam nibh a dui iaculis viverra id a velit. Vivamus egestas risus in magna varius commodo semper viverra egestas.</p><time>Mar10, 2017</time></article>
    <article class="news-item"><h3>Nam fermentum vestibulum purus</h3><p>Duis aliquam nibh a dui iaculis viverra id a velit. Vivamus egestas risus in magna varius commodo semper viverra egestas.</p><time>Mar10, 2017</time></article>
    <div class="news-all">READ ALL NEWS ›</div>
  </div>
</section>

<footer class="abs footer"></footer>
<div class="abs fcol" style="left:75px">
  <h4>SITE MAP</h4>
  <ul><li>Home</li><li>Apply For A Loan</li><li>My Credit Union</li><li>Products &amp; Services</li><li>Become A Member</li><li>Tools &amp; Benefits</li><li>Locations</li></ul>
</div>
<div class="abs fcol" style="left:343px">
  <h4>OUR LOCATIONS</h4>
  <h5>Harbourview</h5>
  <ul><li>Harbour Road &amp; Cedar Lane</li>
  <li><span class="ic"><svg viewBox="0 0 24 24"><path d="M6.6 10.8a15 15 0 0 0 6.6 6.6l2.2-2.2c.3-.3.7-.4 1-.2 1.1.4 2.3.6 3.6.6.6 0 1 .4 1 1V20c0 .6-.4 1-1 1A17 17 0 0 1 3 4c0-.6.4-1 1-1h3.5c.6 0 1 .4 1 1 0 1.3.2 2.5.6 3.6.1.3 0 .7-.2 1z"/></svg></span>Phone: (555) 410-2200</li>
  <li><span class="ic"><svg viewBox="0 0 24 24"><path d="M6 2h10v7h4a2 2 0 0 1 2 2v9a2 2 0 0 1-2 2H4a2 2 0 0 1-2-2v-9a2 2 0 0 1 2-2h2z"/></svg></span>Fax: (555) 410-2291</li></ul>
</div>
<div class="abs fcol" style="left:617px;top:2150px">
  <h5>Port Cedar, Pine Island</h5>
  <ul><li>#8 Pinewood Crescent</li>
  <li><span class="ic"><svg viewBox="0 0 24 24"><path d="M6.6 10.8a15 15 0 0 0 6.6 6.6l2.2-2.2c.3-.3.7-.4 1-.2 1.1.4 2.3.6 3.6.6.6 0 1 .4 1 1V20c0 .6-.4 1-1 1A17 17 0 0 1 3 4c0-.6.4-1 1-1h3.5c.6 0 1 .4 1 1 0 1.3.2 2.5.6 3.6.1.3 0 .7-.2 1z"/></svg></span>Phone: (555) 420-3189</li>
  <li><span class="ic"><svg viewBox="0 0 24 24"><path d="M6 2h10v7h4a2 2 0 0 1 2 2v9a2 2 0 0 1-2 2H4a2 2 0 0 1-2-2v-9a2 2 0 0 1 2-2h2z"/></svg></span>Fax: (555) 420-3036</li></ul>
</div>
<div class="abs fcol" style="left:888px;top:2150px">
  <h5>Eastwood</h5>
  <ul><li>Greenvale Shopping Plaza</li>
  <li><span class="ic"><svg viewBox="0 0 24 24"><path d="M6.6 10.8a15 15 0 0 0 6.6 6.6l2.2-2.2c.3-.3.7-.4 1-.2 1.1.4 2.3.6 3.6.6.6 0 1 .4 1 1V20c0 .6-.4 1-1 1A17 17 0 0 1 3 4c0-.6.4-1 1-1h3.5c.6 0 1 .4 1 1 0 1.3.2 2.5.6 3.6.1.3 0 .7-.2 1z"/></svg></span>Phone: (555) 430-4613</li>
  <li><span class="ic"><svg viewBox="0 0 24 24"><path d="M6 2h10v7h4a2 2 0 0 1 2 2v9a2 2 0 0 1-2 2H4a2 2 0 0 1-2-2v-9a2 2 0 0 1 2-2h2z"/></svg></span>Fax: (555) 430-4612</li></ul>
</div>

<div class="abs bottom">
  <div class="copy">Copyright © 2017 <b>PHFC</b><br>All Rights Reserved. Privacy Policy / Website Terms / USA Patriot Act</div>
  <div class="social" aria-label="Social media links">
    <span aria-label="Social link 1"></span><span aria-label="Social link 2"></span><span aria-label="Social link 3"></span><span aria-label="Social link 4"></span><span aria-label="Social link 5"></span>
  </div>
</div>

</body>
</html>
```